Paint Retail Store needs a logo/label redesign.

We are redesigning a label for one of our products. We are a paint retail store that specializes on selling premium paint at outlet prices called Coat & Gleam. We want the redesign to exude professionalism and cleanliness. Attached is a picture of our current label. We want the logo Coat & Gleam to be modified to a more modern feel that still incorporates the iconic paint roller element that has been part of our brand identity. We want the description of: Exceptional Durability/ Luxurious Finish to be included in the front of the label to attract our clients. Include all of the information and description of the current label to the new label. Attached are pictures of our competitors labels so you have an idea of what we are looking for. We also want the background of the label to be a clean solid color.

Target Market(s)

Home Owners, DIY enthusiasts, Contractors/painters, interior designers

Industry/Entity Type

Paint and Coatings retail store

Colors

Designer to choose colors to be used in the design.

Requirements
Must have
• Semigloss Finish, Exceptional Durability, Luxurios Finish. Include all the information that are on the side of the current label to the new label. Include the phrase: Made in the US.
Nice to have
• A redesign of the logo: Coat & Gleam to convey a more modern/professional look.
Should not have
• Feminine colors.

```html
<!DOCTYPE html>
<html lang="en">
<head>
<meta charset="utf-8">
<title>Coat &amp; Gleam Semi-Gloss Latex Paint Label</title>
<link rel="stylesheet" href="https://fonts.googleapis.com/css2?family=Montserrat:wght@400;600;700;800;900&display=swap">
<style>
:root{
  --page:#e4e6ea;
  --blue-deep:#0c4fb4;
  --blue:#1a6fd6;
  --blue-light:#3d9be9;
  --sky:#6cc2f5;
  --white:#ffffff;
  --ink:#111111;
  --orange:#f59a12;
}
*{margin:0;padding:0;box-sizing:border-box}
html,body{width:878px;height:1200px;overflow:hidden}
body{background:var(--page);font-family:"Montserrat",sans-serif;color:var(--white);position:relative}
.label{position:absolute;left:0;top:280px;width:878px;height:640px;overflow:hidden;
  background:linear-gradient(90deg,var(--blue-deep) 0%,var(--blue) 30%,var(--blue-light) 50%,var(--blue) 70%,var(--blue-deep) 100%)}
.abs{position:absolute}
/* left panel */
.usage{left:30px;top:29px;width:240px;font-size:9px;line-height:11.4px}
.usage p{margin-bottom:10px}
.usage b{font-weight:700}
.usage h3{font-size:11.4px;font-weight:700;margin:2px 0 6px -1px;letter-spacing:.1px}
.ingredients{left:85px;top:538px;width:110px;height:90px;background:var(--white);color:var(--ink);
  border:1.5px solid var(--ink);border-radius:5px;padding:5px 7px;font-size:6.6px;line-height:7.7px}
.ingredients .head{display:flex;justify-content:space-between;font-weight:700;font-size:7px;border-bottom:1px solid var(--ink);padding-bottom:2px;margin-bottom:2px}
.ingredients .row{display:flex;justify-content:space-between}
.ingredients .note{text-align:center;font-weight:700;margin-top:4px;font-size:6.5px;line-height:7px}
.volume{left:218px;top:572px;width:110px;text-align:center;font-size:10.5px;line-height:13px;font-weight:600}
.origin{left:218px;top:604px;width:110px;text-align:center;font-size:8px;line-height:10px;font-weight:800;letter-spacing:.4px}
/* front panel */
.brand{left:297px;top:70px;width:320px;font-weight:900;font-size:66px;line-height:66px;letter-spacing:-1.5px}
.brand-mark{left:300px;top:32px;width:34px;height:34px;background:var(--orange);border-radius:50%}
.tagline{left:300px;top:281px;width:315px;text-align:center;font-size:16.5px;line-height:17px;font-weight:400}
.finish{left:290px;top:338px;width:330px;text-align:center;font-size:49px;font-weight:900;letter-spacing:-.5px;
  text-shadow:0 3px 6px rgba(0,0,0,.3)}
.latex{left:324px;top:412px;width:248px;height:138px}
.latex span{position:absolute;left:40px;top:36px;font-weight:900;font-size:30px;line-height:30px;color:var(--white);transform:rotate(-6deg)}
.durability{left:300px;top:566px;width:310px;text-align:center;font-size:15.5px;line-height:16px;font-weight:800}
.freeze{left:332px;top:603px;width:236px;height:40px;background:var(--sky);border-radius:18px 18px 0 0;
  display:flex;align-items:center;justify-content:center;gap:14px}
.freeze strong{font-size:14px;line-height:12px;font-weight:800;text-align:center}
/* right panel */
.safety{left:645px;top:29px;width:228px}
.safety .center{text-align:center}
.safety h2{font-size:14.5px;line-height:18px;font-weight:800}
.safety .cleanup{font-size:10.4px;line-height:13px;margin:9px 0 11px}
.icons{display:grid;grid-template-columns:repeat(3,38px);column-gap:12px;row-gap:4px;margin:9px 0 0 40px}
.icon .tile{width:38px;height:38px;background:var(--white);border:1px solid var(--ink)}
.icon small{display:block;font-size:4.8px;line-height:5.6px;margin-top:2px;height:12px}
.cautions{font-size:7.9px;line-height:10.8px;margin-top:6px}
.cautions p{margin-bottom:7px}
.cautions p:last-child{margin-bottom:0}
.cautions b{font-weight:800;letter-spacing:-.2px}
</style>
</head>
<body>
<main class="label">

  <section class="abs usage">
    <p><b>Where To Use:</b> Walls, cabinets, ceilings, trim and doors. Use over drywall, wood, concrete/brick, plaster and wallpaper. See bellow for preparation steps.</p>
    <p><b>How Much You Need:</b> For one coat coverage, apply at a maximum of 400 square feet per gallon. Rough or textured urfaces may require more-allow for 125-300 square feet per gallon. Do not thin.</p>
    <p><b>What Tools To Use:</b> May be applied with a quality roller, a nylon/polyester brush, or a paint pad.</p>
    <p><b>How To Apply:</b> Room and surface temperature must be 50 degrees Fahrenheit. Allow at least 4 hours of drying time before recoating. Mix gallons togheter for color and sheen uniformity when using more than one gallon of the same product.</p>
    <p>Care for Freshly Painted Surfaces; Freshly painted surfaced may be washed either 30 days-Until then avoid touching, wiping, or wetting the surface. Then clean with mild, non-abrasive, non-oily cleanser and water. Do not place objects on painted sirfaces untill throughly dry. Soap and Water Cleanup</p>
    <h3>HOW TO PREPARE THE SURFACE</h3>
    <p><b>Previously Painted Surfaces:</b> Remove loose paint, Wash with a mild, non-abrasive, non-oily cleanser and water. Rinse completely, let dry. Patch holes and cracks with speckling paste and let dry. Sand patched area and wipe off residue. Send all smooth or glossy surfaces, rinse well.</p>
    <p><b>Unpainted Surfaces:</b> Wallboard or Drywall. Concrete/brick. Allow new masonry to sure at least 30 days. Etch smooth unpainted concrete. Remove all loose concrete and efflorescence. Rinse and allow to dry Plaster (new)-Must be dried and cured for 30 days. Prime with primer. Let dry 4 hours before top coating. Wallpaper Vinyl coated wallpaper may be coated if all seams and edges are glued tight. Self-sand and wipe clean. Use primer and alllow 24 hours to dry.</p>
  </section>

  <div class="abs ingredients">
    <div class="head"><span>CAS NO.</span><span>Ingredients</span></div>
    <div class="row"><span>7732-18-5</span><span>Water</span></div>
    <div class="row"><span>Propietary</span><span>Vinyl Polymer</span></div>
    <div class="row"><span>13463-67-7</span><span>Titanium Dioxide</span></div>
    <div class="row"><span>Propietary</span><span>Acrylic Polymer</span></div>
    <div class="row"><span>471-34-1</span><span>Calcium Carbonate</span></div>
    <div class="row"><span>14464-46-1</span><span>Cristobalite</span></div>
    <div class="note">NON-PHOTOCHEMICALLY<br>REACTIVE</div>
  </div>

  <div class="abs volume">1 Gal.<br>(124 OZ/3.667 Lts.)</div>
  <p class="abs origin">MADE IN THE US</p>

  <div class="abs brand-mark"></div>
  <h1 class="abs brand">Coat<br>&amp; Gleam</h1>

  <p class="abs tagline">PREMIUM PAINT AT OUTLET<br>PRICES SEMI-GLOSS</p>
  <p class="abs finish">SEMI-GLOSS</p>

  <div class="abs latex">
    <svg width="248" height="138" viewBox="0 0 248 138" role="img" aria-label="Latex paint banner with paint roller artwork">
      <rect x="8" y="20" width="220" height="95" rx="6" fill="#5bb6f0" transform="rotate(-6 124 68)"/>
    </svg>
    <span>LATEX<br>&nbsp;&nbsp;&nbsp;PAINT</span>
  </div>

  <p class="abs durability">EXCEPTIONAL DURABILITY &amp;<br>LUXURIOUS FINISH</p>

  <div class="abs freeze">
    <svg width="18" height="18" viewBox="0 0 18 18" aria-hidden="true"><g stroke="#fff" stroke-width="2" stroke-linecap="round"><line x1="9" y1="1" x2="9" y2="17"/><line x1="2" y1="5" x2="16" y2="13"/><line x1="2" y1="13" x2="16" y2="5"/></g></svg>
    <strong>PROTECT FROM<br>FREEZING</strong>
    <svg width="18" height="18" viewBox="0 0 18 18" aria-hidden="true"><g stroke="#fff" stroke-width="2" stroke-linecap="round"><line x1="9" y1="1" x2="9" y2="17"/><line x1="2" y1="5" x2="16" y2="13"/><line x1="2" y1="13" x2="16" y2="5"/></g></svg>
  </div>

  <section class="abs safety">
    <h2 class="center">SOLID VINYL WALLPAPER<br>CANNOT BE PAINTED.</h2>
    <p class="center cleanup">Cleanup: Clean tools, spills and splatters immediately with soap and water</p>
    <h2 class="center">KEEP FROM FREEZING-DO<br>NOT THIN</h2>
    <div class="icons">
      <div class="icon"><div class="tile" role="img" aria-label="Pictogram: clean, dull and dry surface"></div><small>Clean, dull and dry surface</small></div>
      <div class="icon"><div class="tile" role="img" aria-label="Pictogram: stir paint thoroughly"></div><small>Stir paint thoroughly</small></div>
      <div class="icon"><div class="tile" role="img" aria-label="Pictogram: start at ceiling edge"></div><small>Start at ceiling edge</small></div>
      <div class="icon"><div class="tile" role="img" aria-label="Pictogram: paint N pattern, fill in"></div><small>Paint "N" pattern - still in</small></div>
      <div class="icon"><div class="tile" role="img" aria-label="Pictogram: paint trim last"></div><small>Paint trim last</small></div>
      <div class="icon"><div class="tile" role="img" aria-label="Pictogram: soap and water clean up"></div><small>Soap and water clean up</small></div>
    </div>
    <div class="cautions">
      <p><b>CAUTIONS CONTAINS CRYSTALLINE SILICA-</b> Use only with adecuate ventilation. To avoid overexposure, open windows and doors or use other means to ensure fresh air entry during plication and drying. If you experience eye watering, headaches, or dizzyness, increase fresh air, or wear respiratory protection or leavethe area. Adecuate ventilation required when sending or abrading the dried film. If adequate ventilation cannot ve provided wear an approved particulate respirator. Follow resporator manufacturer's directions for respirator use. Avoid contact with eyes and skin. Wash hands after using. Keep container closed when not in use. Do not transfer contents to other containers for storage</p>
      <p><b>FIRST AID:</b> In case of eye contact, flush thoroughly with large amounts of water. Get medical attention if tirritation persists. If allowed, call Poison Control Center, hospital emergency room, or phisician Inmediately.</p>
      <p><b>DELAYED EFFECTS FROM LONG TERM OVEREXPOSURE.</b> Abrading or sanding of the dry film may release crystaline silica which has been shown to cause lung damage and cancer under long term exposure.</p>
      <p><b>WARNING:</b> This product contains chemicals known to the State of California to cause cancer and birth defects or other reproductive harm.</p>
      <p><b>DO NOT TAKE INTERNALLY<br>KEEP OUT OF THE REACH OF CHILDREN.</b></p>
    </div>
  </section>

</main>
</body>
</html>
```